RWT Fittings Ltd Business Cards

We need a business card with our business logo. We provide window and door installations on high-rises in west coast British Colombia, Canada.

I would like my business information and details on one side of the card, and the other side the company name with logo

Target Market(s)

General Contractors

Industry/Entity Type

Construction

Contact Information for Business Card

one side i want my company name and logo in the dark theme logo that i provided

Requirements
Must have
• Marco Peltieri, 16045518293, RWTFittings@mailbox-demo.com, 1407-5194 Linden Row Burnaby BC, V5H 2K9, Owner & Manager

```html
<!DOCTYPE html>
<html lang="en">
<head>
<meta charset="utf-8">
<title>RWT Fittings Ltd Business Cards</title>
<link rel="stylesheet" href="https://fonts.googleapis.com/css2?family=Roboto:wght@400;500;700&display=swap">
<style>
  :root {
    --page-bg: #232323;
    --card-bg: #1f1f23;
    --deco-dark: #0c0c0e;
    --deco-mid: #2a2a2e;
    --brand-blue: #29a8e0;
    --name-grey: #a3a3a3;
    --text-white: #f2f2f2;
    --back-mark: #3a3a3f;
  }
  * { box-sizing: border-box; margin: 0; padding: 0; }
  html, body {
    width: 1200px;
    height: 780px;
    overflow: hidden;
    background: var(--page-bg);
    font-family: "Roboto", Arial, sans-serif;
  }
  .card-pair {
    position: absolute;
    inset: 0;
    display: flex;
    align-items: center;
    justify-content: center;
    gap: 40px;
  }
  .card {
    position: relative;
    width: 540px;
    height: 308px;
    background: var(--card-bg);
    overflow: hidden;
    box-shadow: 0 18px 40px rgba(0,0,0,0.45);
  }

  /* Details side */
  .decoration {
    position: absolute;
    left: 0;
    top: 0;
    width: 540px;
    height: 308px;
  }
  .details {
    position: absolute;
    right: 34px;
    top: 34px;
    width: 270px;
    text-align: right;
  }
  .company-mark {
    display: flex;
    align-items: center;
    justify-content: flex-end;
    gap: 10px;
    margin-bottom: 26px;
  }
  .company-mark__square {
    width: 14px;
    height: 14px;
    background: var(--brand-blue);
  }
  .company-mark__name {
    font-weight: 700;
    font-size: 20px;
    color: var(--brand-blue);
    letter-spacing: 0.5px;
  }
  .person-name {
    font-weight: 700;
    font-size: 25px;
    line-height: 1.1;
    color: var(--name-grey);
  }
  .person-name__first { color: var(--brand-blue); }
  .person-role {
    font-weight: 500;
    font-size: 13px;
    color: var(--text-white);
    margin-top: 3px;
    margin-bottom: 16px;
  }
  .contact-line {
    font-size: 12.5px;
    line-height: 1.45;
    color: var(--text-white);
  }
  .contact-line--spaced { margin-top: 10px; }
  .contact-row {
    display: flex;
    align-items: center;
    justify-content: flex-end;
    gap: 8px;
  }
  .contact-icon { width: 13px; height: 13px; flex: none; }
  .accent-bar {
    position: absolute;
    right: 0;
    top: 142px;
    width: 10px;
    height: 52px;
    background: var(--brand-blue);
  }

  /* Company side */
  .card--back {
    display: flex;
    align-items: center;
    justify-content: center;
  }
  .back-mark {
    display: flex;
    align-items: center;
    gap: 16px;
  }
  .back-mark__square {
    width: 30px;
    height: 30px;
    background: var(--back-mark);
  }
  .back-mark__name {
    font-weight: 700;
    font-size: 36px;
    color: var(--back-mark);
    letter-spacing: 1px;
  }
</style>
</head>
<body>
<main class="card-pair">

  <section class="card card--details" aria-label="Business card, contact side">
    <svg class="decoration" viewBox="0 0 540 308" role="img" aria-label="Large faint company emblem decoration">
      <defs>
        <linearGradient id="decoFill" x1="0" y1="0" x2="1" y2="0.3">
          <stop offset="0" stop-color="var(--deco-dark)"/>
          <stop offset="0.7" stop-color="#111114"/>
          <stop offset="1" stop-color="var(--deco-mid)"/>
        </linearGradient>
      </defs>
      <polygon points="0,0 300,0 200,308 0,308" fill="url(#decoFill)"/>
    </svg>

    <div class="details">
      <div class="company-mark">
        <span class="company-mark__square"></span>
        <span class="company-mark__name">RWT Fittings Ltd</span>
      </div>
      <h1 class="person-name"><span class="person-name__first">Marco</span> Peltieri</h1>
      <p class="person-role">Owner &amp; Manager</p>
      <p class="contact-line">1407-5194 Linden Row</p>
      <p class="contact-line">Burnaby BC, V5H 2K9</p>
      <p class="contact-line contact-line--spaced contact-row">
        <span>1604 551 8293</span>
        <svg class="contact-icon" viewBox="0 0 24 24" aria-hidden="true">
          <path d="M6.6 10.8a15.1 15.1 0 0 0 6.6 6.6l2.2-2.2a1 1 0 0 1 1-.25 11.4 11.4 0 0 0 3.6.57 1 1 0 0 1 1 1V20a1 1 0 0 1-1 1A17 17 0 0 1 3 4a1 1 0 0 1 1-1h3.5a1 1 0 0 1 1 1c0 1.25.2 2.45.57 3.57a1 1 0 0 1-.25 1z" fill="var(--brand-blue)"/>
        </svg>
      </p>
      <p class="contact-line contact-row">
        <span>RWTFittings@mailbox-demo.com</span>
        <svg class="contact-icon" viewBox="0 0 24 24" aria-hidden="true">
          <rect x="2" y="5" width="20" height="14" rx="1.5" fill="var(--brand-blue)"/>
          <path d="M3 6.5l9 6.5 9-6.5" fill="none" stroke="var(--card-bg)" stroke-width="1.8"/>
        </svg>
      </p>
    </div>

    <span class="accent-bar"></span>
  </section>

  <section class="card card--back" aria-label="Business card, company side">
    <div class="back-mark">
      <span class="back-mark__square"></span>
      <span class="back-mark__name">RWT Fittings Ltd</span>
    </div>
  </section>

</main>
</body>
</html>
```